A website for a Maltese Law Firm

Our law firm needs a website to further its business. The site should have a simple yet effective design. We would need the following sections: About us, Practice Areas, About Malta, Contact. These should be further split as follows:

About us: Our firm, Our values, What others say, Offices

Practice Areas: Crimimal, Citizenship & Residence, Sovereign Patron Pathway, Criminal Defence, Civil Litigation, Arbitration and ADR, Commercial and Corporate, Media Law.

About Malta: just one section.

Contact: Just one section

We would also need a news feed at the front of the site to include latest news regarding our cases.

At the bottom we need a section for our Terms and a Privacy Statement.

Our logo is being attached.

Target Market(s)

All clients looking for legal assistance in Malta

Industry/Entity Type

Legal

Coding

Coded - Design and coding required

Number of Pages Required

1 page

Requirements
Must have
• It must be simple yet striking.

```html
<!DOCTYPE html>
<html lang="en">
<head>
<meta charset="utf-8">
<title>Mercieca &amp; Galea Advocates</title>
<link rel="stylesheet" href="https://fonts.googleapis.com/css2?family=Cinzel:wght@400;700&family=Open+Sans:ital,wght@0,400;0,600;0,700;1,700&display=swap">
<style>
:root{
  --ink:#222222;
  --black:#000000;
  --charcoal:#2b2b2b;
  --panel:#f1f1f1;
  --white:#ffffff;
  --muted:#555555;
  --rule:#cfcfcf;
  --gray-link:#bdbdbd;
  --footer:#141414;
  --copyband:#5a5a5a;
}
*{box-sizing:border-box;margin:0;padding:0}
html,body{width:1200px;height:2848px;overflow:hidden}
body{background:var(--white);font-family:"Open Sans",Arial,sans-serif;color:var(--ink);position:relative}
.serif{font-family:"Cinzel",Georgia,serif}

/* header */
.site-header{height:140px;display:flex;align-items:center;justify-content:space-between;padding:0 58px 0 46px}
.brand-name{font-family:"Cinzel",Georgia,serif;font-size:38px;font-weight:400;color:var(--ink);letter-spacing:1px}
.header-contacts{display:flex;gap:36px;align-items:center;font-size:15px;font-weight:600;color:#555}
.contact-item{display:flex;align-items:center;gap:10px;line-height:1.35}

/* nav */
.main-nav{height:46px;background:var(--black);display:flex;padding-left:164px}
.main-nav a{font-family:"Cinzel",Georgia,serif;color:var(--white);text-decoration:none;font-size:16px;display:flex;align-items:center;padding:0 38px;height:46px;gap:6px}
.main-nav a.active{background:#444}

/* hero */
.hero{position:relative;height:500px;background:linear-gradient(100deg,#4a2a17 0%,#7b4a2a 30%,#a8734a 55%,#6b4127 80%,#3b2214 100%)}
.consult-form{position:absolute;left:735px;top:63px;width:400px;height:375px;border:2px solid rgba(255,255,255,.75);border-radius:6px;background:rgba(255,255,255,.22)}
.consult-title{position:absolute;left:-12px;top:22px;width:420px;height:48px;background:var(--black);color:var(--white);font-family:"Cinzel",Georgia,serif;font-size:18px;display:flex;align-items:center;justify-content:center;letter-spacing:.5px}
.form-grid{position:absolute;left:20px;top:92px;width:360px;display:grid;grid-template-columns:1fr 1fr;gap:10px}
.field{height:30px;background:rgba(40,40,40,.85);color:#f3f3f3;font-size:12px;padding:7px 12px}
.field.wide{grid-column:1/3;height:132px}
.submit-btn{position:absolute;left:98px;bottom:26px;width:204px;height:32px;background:var(--black);color:var(--white);font-size:13px;font-weight:700;display:flex;align-items:center;justify-content:center}

/* intro band */
.intro-band{height:152px;background:var(--charcoal);display:flex;align-items:center;justify-content:center;padding:0 70px}
.intro-band p{font-family:"Cinzel",Georgia,serif;color:#e8e8e8;font-size:18px;line-height:1.4;text-align:center}

/* section titles */
.section-title{font-family:"Cinzel",Georgia,serif;font-size:30px;color:var(--ink);text-align:center;display:inline-block;border-top:2px solid var(--ink);border-bottom:2px solid var(--ink);padding:4px 4px 6px;letter-spacing:.5px}
.title-wrap{text-align:center}

/* practice areas */
.practice{position:relative;height:775px}
.practice .title-wrap{position:absolute;top:50px;width:100%}
.area-card{position:absolute;width:228px;height:145px;padding:4px;background:var(--white);box-shadow:0 0 0 1px #e2e2e2,0 2px 4px rgba(0,0,0,.08)}
.area-photo{width:100%;height:100%;position:relative}
.area-label{position:absolute;left:0;right:0;height:28px;background:rgba(30,30,30,.72);color:var(--white);font-family:"Cinzel",Georgia,serif;font-size:17px;display:flex;align-items:center;justify-content:center}
.top .area-label{top:0}
.bottom .area-label{bottom:0}
.diagram{position:absolute;left:0;top:0}
.hub{position:absolute;left:422px;top:385px;width:356px;height:88px;border:2px solid var(--ink);border-radius:8px;background:var(--white);display:flex;align-items:center;justify-content:center;font-family:"Cinzel",Georgia,serif;font-size:30px;color:var(--ink)}

/* about malta */
.about-malta{position:relative;height:498px;background:var(--panel)}
.about-malta .title-wrap{position:absolute;top:50px;width:100%}
.malta-photo{position:absolute;left:70px;top:122px;width:507px;height:312px;padding:6px;background:var(--white);box-shadow:0 1px 4px rgba(0,0,0,.2)}
.malta-photo div{width:100%;height:100%;background:linear-gradient(180deg,#3f6fb5 0%,#8fb1d8 25%,#d9c79a 42%,#c4a977 55%,#7fc4c2 70%,#a9ddd6 100%)}
.malta-copy{position:absolute;left:657px;top:132px;width:470px;font-size:16px;line-height:1.45;color:#444}
.more-btn{display:inline-block;margin-top:26px;background:var(--charcoal);color:var(--white);font-weight:700;font-size:16px;padding:9px 24px;border-radius:6px}

/* testimonials */
.testimonials{position:relative;height:360px}
.testimonials .title-wrap{position:absolute;top:48px;width:100%}
.client-avatar{position:absolute;left:86px;top:132px;width:128px;height:128px;border-radius:50%;border:5px solid #555;background:linear-gradient(160deg,#e9d6b8,#c9a37a)}
.avatar-tip{position:absolute;left:214px;top:186px}
.quote{position:absolute;left:262px;top:138px;width:840px;font-size:15px;line-height:1.5;color:#222}
.quote-mark{position:absolute;font-family:Georgia,serif;font-size:72px;font-weight:700;line-height:1;color:var(--ink)}
.quote-text{padding-left:52px}
.quote-author{font-style:italic;font-weight:700;font-size:18px;margin:20px 0 0 62px}
.slider-dots{position:absolute;top:282px;left:0;width:100%;display:flex;justify-content:center;gap:6px}
.slider-dots span{width:12px;height:12px;border-radius:50%;border:1.5px solid #777}

/* footer */
.site-footer{position:relative;height:323px;background:var(--footer);color:var(--white)}
.footer-col{position:absolute;top:40px}
.footer-col h4{font-size:15px;font-weight:700;margin-bottom:14px;letter-spacing:.3px}
.footer-col li{list-style:none;font-size:12.5px;font-weight:600;color:var(--gray-link);line-height:20.5px;text-transform:uppercase}
.office{display:flex;align-items:center;gap:8px;font-size:13px;font-weight:600;color:var(--gray-link);margin-bottom:12px}
.footer-brand{position:absolute;left:852px;top:120px;font-family:"Cinzel",Georgia,serif;font-size:28px;color:var(--white)}
.copyright{height:54px;background:var(--copyband);color:#e6e6e6;font-size:10.5px;font-weight:700;display:flex;align-items:center;justify-content:center;letter-spacing:.3px}
</style>
</head>
<body>

<header class="site-header">
  <div class="brand-name">Mercieca &amp; Galea</div>
  <div class="header-contacts">
    <div class="contact-item">
      <svg width="30" height="30" viewBox="0 0 30 30"><circle cx="15" cy="15" r="13" fill="none" stroke="#777" stroke-width="2"/><path d="M10 8l3 0 1.5 4-2 1.5c1 2 2.5 3.5 4 4l1.5-2 4 1.5 0 3c-6 .5-12.5-6-12-12z" fill="#777"/></svg>
      <div>(356) 2000 1140 - Valletta<br>(356) 2000 2280 - Birkirkara</div>
    </div>
    <div class="contact-item">
      <svg width="30" height="30" viewBox="0 0 30 30"><circle cx="15" cy="15" r="13" fill="none" stroke="#777" stroke-width="2"/><rect x="8" y="10" width="14" height="10" fill="none" stroke="#777" stroke-width="1.8"/><path d="M8 10l7 6 7-6" fill="none" stroke="#777" stroke-width="1.8"/></svg>
      <div>info@mgadvocates.com</div>
    </div>
  </div>
</header>

<nav class="main-nav">
  <a class="active">Home</a>
  <a>About us <svg width="10" height="8" viewBox="0 0 10 8"><path d="M1 1l4 5 4-5" fill="none" stroke="#fff" stroke-width="2"/></svg></a>
  <a>Practice Areas <svg width="10" height="8" viewBox="0 0 10 8"><path d="M1 1l4 5 4-5" fill="none" stroke="#fff" stroke-width="2"/></svg></a>
  <a>About Malta</a>
  <a>Contact</a>
</nav>

<section class="hero" role="img" aria-label="Photo of scales of justice, a wooden gavel and open law books">
  <form class="consult-form">
    <div class="consult-title">Send a message for free consultation</div>
    <div class="form-grid">
      <div class="field">First Name</div>
      <div class="field">Last Name</div>
      <div class="field">Email Address</div>
      <div class="field">Phone Number</div>
      <div class="field wide">Message</div>
    </div>
    <div class="submit-btn">SUBMIT</div>
  </form>
</section>

<section class="intro-band">
  <p>Lorem ipsum dolor sit amet, consectetuer adipiscing elit, sed diam nonummy nibh euismod tincidunt ut laoreet dolore magna aliquamerat volutpat. Ut wisi enim ad minim veniam, quis nostrud exerci tation ullamcorper suscipit lobortis nisl ut aliquip ex ea commodo consequat.</p>
</section>

<section class="practice">
  <div class="title-wrap"><h2 class="section-title">Practice Areas</h2></div>

  <div class="area-card top" style="left:101px;top:152px"><div class="area-photo" role="img" aria-label="Photo of a burning car" style="background:linear-gradient(160deg,#3a2a1c,#d8691c 55%,#f2b441)"><div class="area-label">Criminal</div></div></div>
  <div class="area-card top" style="left:359px;top:152px"><div class="area-photo" role="img" aria-label="Photo of a hand holding a passport" style="background:linear-gradient(160deg,#4b5a70,#a8b6c8 50%,#3d5a8a)"><div class="area-label">Citizenship</div></div></div>
  <div class="area-card top" style="left:614px;top:152px"><div class="area-photo" role="img" aria-label="Photo of investors in a business meeting" style="background:linear-gradient(160deg,#d6dde6,#8aa0b8 50%,#3f4e66)"><div class="area-label">Sovereign Patron</div></div></div>
  <div class="area-card top" style="left:872px;top:152px"><div class="area-photo" role="img" aria-label="Photo of handcuffed hands behind a suit" style="background:linear-gradient(160deg,#2a2a2e,#5a5a62 50%,#1c1c20)"><div class="area-label">Criminal Defence</div></div></div>

  <div class="area-card bottom" style="left:101px;top:566px"><div class="area-photo" role="img" aria-label="Photo of brass scales on a desk" style="background:linear-gradient(160deg,#3a2414,#9a6a3a 50%,#5c3a1e)"><div class="area-label">Civil Litigation</div></div></div>
  <div class="area-card bottom" style="left:359px;top:566px"><div class="area-photo" role="img" aria-label="Photo of an arbitration hearing document and pen" style="background:linear-gradient(160deg,#e8e4dc,#c7bfae 50%,#8a6a40)"><div class="area-label">Arbitration &amp; ADR</div></div></div>
  <div class="area-card bottom" style="left:614px;top:566px"><div class="area-photo" role="img" aria-label="Photo of a corporate team in an office" style="background:linear-gradient(160deg,#e2e8ef,#8fa5bf 50%,#2f3e57)"><div class="area-label">Commercial</div></div></div>
  <div class="area-card bottom" style="left:872px;top:566px"><div class="area-photo" role="img" aria-label="Photo of a hand signing a paper" style="background:linear-gradient(160deg,#5a4a3a,#cdbba3 50%,#7a6248)"><div class="area-label">Media Law</div></div></div>

  <svg class="diagram" width="1200" height="775" viewBox="0 0 1200 775">
    <g stroke="#333" stroke-width="2" stroke-dasharray="2 4" fill="none">
      <line x1="215" y1="289" x2="422" y2="400"/>
      <line x1="473" y1="289" x2="540" y2="385"/>
      <line x1="728" y1="289" x2="660" y2="385"/>
      <line x1="986" y1="289" x2="778" y2="400"/>
      <line x1="215" y1="562" x2="422" y2="460"/>
      <line x1="473" y1="562" x2="540" y2="473"/>
      <line x1="728" y1="562" x2="660" y2="473"/>
      <line x1="986" y1="562" x2="778" y2="460"/>
    </g>
    <g fill="#333" stroke="#fff" stroke-width="5">
      <circle cx="215" cy="289" r="30"/><circle cx="473" cy="289" r="30"/><circle cx="728" cy="289" r="30"/><circle cx="986" cy="289" r="30"/>
      <circle cx="215" cy="562" r="30"/><circle cx="473" cy="562" r="30"/><circle cx="728" cy="562" r="30"/><circle cx="986" cy="562" r="30"/>
    </g>
    <g fill="none" stroke="#fff" stroke-width="2.5" stroke-linecap="round">
      <!-- gavel -->
      <path d="M206 282l12-8M210 288l12-8M213 284l-10 12M205 300h20"/>
      <!-- passport -->
      <rect x="464" y="277" width="14" height="20" rx="1"/><circle cx="471" cy="285" r="3"/><rect x="474" y="281" width="8" height="14" rx="1"/>
      <!-- handshake -->
      <path d="M716 292l8-8 6 4 10-8M722 296l6 4M716 292l6 4"/>
      <!-- handcuffs -->
      <circle cx="978" cy="296" r="6"/><circle cx="994" cy="282" r="6"/><path d="M982 292l8-6"/>
      <!-- scales -->
      <path d="M215 548v26M203 552h24M207 574h16M203 552l-5 10h10zM227 552l-5 10h10z"/>
      <!-- person at lectern -->
      <circle cx="470" cy="550" r="4"/><path d="M464 562h16v12h-16zM470 556v6"/>
      <!-- building -->
      <rect x="718" y="552" width="10" height="22"/><rect x="728" y="546" width="10" height="28"/>
      <!-- document -->
      <rect x="976" y="550" width="20" height="24" rx="1"/><path d="M980 556h12M980 562h12M980 568h8"/>
    </g>
  </svg>
  <div class="hub">Mercieca &amp; Galea</div>
</section>

<section class="about-malta">
  <div class="title-wrap"><h2 class="section-title">About Malta</h2></div>
  <div class="malta-photo"><div role="img" aria-label="Photo of a Maltese harbour with colourful fishing boats and limestone houses"></div></div>
  <div class="malta-copy">
    <p>Nam liber tempor cum soluta nobis eleifend option congue nihil imperdiet doming id quod mazim placerat facer possim assum. Typi non habent claritatem insitam; est usus legentis in iis qui facit eorum claritatem. Investigationes demonstrav erunt lectores legere me lius quod ii legunt saepius. Claritas est etiam processus dynamicus, qui sequitur mutationem consuetudium lectorum.</p>
    <span class="more-btn">More about Malta</span>
  </div>
</section>

<section class="testimonials">
  <div class="title-wrap"><h2 class="section-title">Clients Testimonials</h2></div>
  <div class="client-avatar" role="img" aria-label="Portrait of the client"></div>
  <svg class="avatar-tip" width="14" height="22" viewBox="0 0 14 22"><path d="M0 0l14 11-14 11z" fill="#555"/></svg>
  <div class="quote">
    <span class="quote-mark" style="left:-2px;top:-4px">&#8221;</span>
    <p class="quote-text">Lorem ipsum dolor sit amet, consectetuer adipiscing elit, sed diam nonummy nibh euismod tincidunt ut laoreet dolore magna aliquam erat volu. Wisi enim ad minim veniam, quis nostrud exerci tation ullamcorper suscipit obortis nisl ut aliquip ex ea commodo consequat.</p>
    <span class="quote-mark" style="left:410px;top:44px">&#8221;</span>
    <p class="quote-author">Helen Marsh</p>
  </div>
  <div class="slider-dots"><span></span><span></span><span></span></div>
</section>

<footer class="site-footer">
  <div class="footer-col" style="left:58px">
    <h4>QUICK LINKS</h4>
    <ul><li>Home</li><li>About us</li><li>Practice Areas</li><li>About Malta</li><li>Contact</li></ul>
  </div>
  <div class="footer-col" style="left:252px">
    <h4>PRACTICE AREAS</h4>
    <ul><li>Criminal</li><li>Citizenship &amp; Residence</li><li>Sovereign Patron Pathway</li><li>Criminal Defence</li><li>Civil Litigation</li><li>Arbitration &amp; ADR</li><li>Commercial &amp; Corporate</li><li>Media Law</li></ul>
  </div>
  <div class="footer-col" style="left:585px">
    <h4>VALETTA</h4>
    <div class="office"><svg width="20" height="20" viewBox="0 0 20 20"><circle cx="10" cy="10" r="8.5" fill="none" stroke="#bbb" stroke-width="1.5"/><path d="M10 5a3.5 3.5 0 0 1 3.5 3.5c0 2.5-3.5 6-3.5 6s-3.5-3.5-3.5-6A3.5 3.5 0 0 1 10 5z" fill="#bbb"/></svg>12/4, HARBOUR LANE</div>
    <div class="office"><svg width="20" height="20" viewBox="0 0 20 20"><circle cx="10" cy="10" r="8.5" fill="none" stroke="#bbb" stroke-width="1.5"/><path d="M7 5.5h2l1 2.5-1.3 1c.6 1.3 1.5 2.2 2.6 2.6l1-1.3 2.5 1v2c-4 .3-8.1-3.8-7.8-7.8z" fill="#bbb"/></svg>(356) 2000 1140</div>
    <h4 style="margin-top:22px">BIRKIRKARA</h4>
    <div class="office"><svg width="20" height="20" viewBox="0 0 20 20"><circle cx="10" cy="10" r="8.5" fill="none" stroke="#bbb" stroke-width="1.5"/><path d="M10 5a3.5 3.5 0 0 1 3.5 3.5c0 2.5-3.5 6-3.5 6s-3.5-3.5-3.5-6A3.5 3.5 0 0 1 10 5z" fill="#bbb"/></svg>88, OLIVE GROVE STREET</div>
    <div class="office"><svg width="20" height="20" viewBox="0 0 20 20"><circle cx="10" cy="10" r="8.5" fill="none" stroke="#bbb" stroke-width="1.5"/><path d="M7 5.5h2l1 2.5-1.3 1c.6 1.3 1.5 2.2 2.6 2.6l1-1.3 2.5 1v2c-4 .3-8.1-3.8-7.8-7.8z" fill="#bbb"/></svg>(356) 2000 2280</div>
    <div class="office" style="margin-top:30px"><svg width="20" height="20" viewBox="0 0 20 20"><circle cx="10" cy="10" r="8.5" fill="none" stroke="#bbb" stroke-width="1.5"/><rect x="5.5" y="7" width="9" height="6.5" fill="none" stroke="#bbb" stroke-width="1.3"/><path d="M5.5 7l4.5 4 4.5-4" fill="none" stroke="#bbb" stroke-width="1.3"/></svg>info@mgadvocates.com</div>
  </div>
  <div class="footer-brand">Mercieca &amp; Galea</div>
</footer>
<div class="copyright">COPYRIGHT © 2016 MERCIECA &amp; GALEA ADVOCATES. ALL RIGHTS RESERVED.</div>

</body>
</html>
```